Website for steady harbor detailing.

Need a homepage, pages for: car and truck detailing, boat detailing, airplane detailing, about us, contact us. I have the domain name through nimbushelm so I will need the design uploaded on my domain. Also hoping to link other domains to this page.I would like to see the logo more pronounced. I would like to see a large phone number link to call my business. The layout looks nice but the pics need to depict car washing and waxing not car mechanics. i would like the colors of the webpage to incorporate the colors found in the logo in some way. I would like links to social media pages
Updates

Target Market(s)

Local customers in Vero Beach, Florida.

Number of Pages Required

5+ page

Colors

Requirements
Must have
• Easy to navigate, attractive pages with pictures and logo, professional looking. must have my phone number and logo very prevalent and links to call or go to home page. I would like links to my social media accounts on the home page.
Nice to have
• Easy to navigate, attractive pages with pictures and logo, professional looking.

```html
<!DOCTYPE html>
<html lang="en">
<head>
<meta charset="utf-8">
<title>Steady Harbor Detailing – About Us</title>
<link rel="stylesheet" href="https://fonts.googleapis.com/css2?family=Montserrat:wght@400;500;600;700;800&family=Open+Sans:wght@400;600&display=swap">
<style>
:root{
  --blue:#1e8fe8;
  --blue-deep:#1560c8;
  --navy:#1b2a8a;
  --navy-dark:#14206b;
  --red:#e4332f;
  --white:#ffffff;
  --ink:#1a1a1a;
  --dark:#16181d;
  --grey:#6b6f78;
}
*{box-sizing:border-box;margin:0;padding:0}
html,body{width:1200px;height:4100px;overflow:hidden;background:var(--white)}
body{font-family:"Montserrat",sans-serif;color:var(--ink)}
.canvas{position:relative;width:1200px;height:4100px;overflow:hidden}
.abs{position:absolute}

/* header */
.site-header{left:0;top:0;width:1200px;height:142px;background:var(--white);z-index:5}
.header-band{left:0;top:0}
.brand{left:40px;top:30px;display:flex;align-items:center;gap:14px}
.brand-dot{width:44px;height:44px;border-radius:50%;background:var(--blue-deep)}
.brand-name{font-weight:800;font-size:30px;color:var(--blue-deep);line-height:1.05;width:260px}
.header-phone{left:578px;top:12px;display:flex;align-items:center;gap:10px;color:var(--white);font-weight:700;font-size:40px;line-height:48px;white-space:nowrap}
.social-top{left:958px;top:16px;display:flex;gap:8px}
.social-top span{width:40px;height:40px;border-radius:50%;background:var(--white);opacity:.9}
.social-top span:nth-child(3){background:var(--red);opacity:1}
.main-nav{left:500px;top:86px;display:flex;height:56px;align-items:center}
.main-nav a{color:var(--white);text-decoration:none;font-weight:700;font-size:21px;padding:0 34px;height:56px;line-height:56px;white-space:nowrap}
.main-nav a.active{background:var(--blue)}

/* dark photo areas */
.photo-dark{background:radial-gradient(ellipse at 60% 60%,#3b3f47 0%,#22252b 55%,#121317 100%)}
.about-bg{left:0;top:142px;width:1200px;height:1211px}
.about-title{left:0;top:280px;width:1200px;text-align:center;color:var(--white);font-weight:700;font-size:64px}
.story-tag{left:0;top:365px;width:1200px;display:flex;justify-content:center;align-items:center;gap:12px;color:var(--white);font-size:26px;font-weight:500}
.story-tag i{display:block;width:95px;height:3px;background:var(--white)}
.about-copy{left:142px;top:428px;width:916px;color:var(--white);font-family:"Open Sans",sans-serif;font-size:13.6px;line-height:20.5px;text-align:justify}
.about-copy p{margin-bottom:20px}
.mech-title{left:0;top:1080px;width:1200px;text-align:center;color:var(--white);font-weight:700;font-size:60px}

.mech-card{top:1216px;width:257px;height:347px;background:var(--white);box-shadow:0 4px 12px rgba(0,0,0,.35);padding:11px}
.mech-photo{width:235px;height:255px;background:linear-gradient(160deg,#c9c3bb,#8a8f99 55%,#2f4aa8)}
.mech-name{margin-top:18px;text-align:center;color:var(--navy);font-size:20px;font-weight:500}
.mech-role{text-align:center;color:var(--navy);font-size:11px;margin-top:4px}

/* appointment box */
.work-bg{left:0;top:1850px;width:1200px;height:1020px}
.booking{left:213px;top:1599px;width:771px;height:374px;background:var(--white);box-shadow:0 4px 14px rgba(0,0,0,.3);z-index:3}
.select{top:49px;width:352px;height:60px;border:3px solid var(--navy);background:#e9edf6;box-shadow:inset 0 0 0 3px var(--white);color:var(--navy);font-weight:700;font-size:20px;display:flex;align-items:center;justify-content:center;gap:10px}
.select .caret{position:absolute;right:22px;font-size:16px}
.btn{top:136px;width:352px;height:62px;color:var(--white);font-weight:700;font-size:20px;display:flex;align-items:center;justify-content:center;letter-spacing:.5px}
.btn-blue{left:22px;background:var(--blue)}
.btn-red{left:399px;background:var(--red)}
.call-label{left:0;top:212px;width:771px;text-align:center;color:var(--red);font-weight:800;font-size:32px}
.call-number{left:0;top:252px;width:771px;text-align:center;color:var(--blue);font-weight:800;font-size:84px;text-shadow:3px 4px 4px rgba(0,0,0,.3);letter-spacing:1px;white-space:nowrap}

/* what we do */
.work-title{left:0;top:2083px;width:1200px;text-align:center;color:var(--white);font-weight:700;font-size:44px}
.work-copy{left:60px;top:2148px;width:1080px;text-align:center;color:var(--white);font-family:"Open Sans",sans-serif;font-size:21px;line-height:28px}
.service{width:260px;text-align:center;color:var(--white);font-weight:700;font-size:21px}
.service svg{display:block;margin:0 auto 14px}

/* who we are */
.who-title{left:0;top:2910px;width:1200px;text-align:center;color:var(--navy);font-weight:700;font-size:46px}
.who-copy{left:190px;top:2982px;width:820px;text-align:center;font-family:"Open Sans",sans-serif;font-size:20px;line-height:27px;color:var(--ink)}
.care{top:3060px;width:260px;text-align:center}
.care svg{display:block;margin:0 auto}
.care h3{margin-top:20px;color:var(--blue);font-weight:700;font-size:24px}
.care p{font-family:"Open Sans",sans-serif;font-size:15px;line-height:19px;margin-top:4px;color:var(--ink)}

/* footer */
.footer-bg{left:0;top:3465px;width:1200px;height:635px;background:radial-gradient(ellipse at 40% 55%,#4a4e56 0%,#26292f 55%,#131418 100%)}
.foot-col{top:3538px;color:var(--white)}
.foot-col h4{font-weight:700;font-size:34px;margin-bottom:40px;white-space:nowrap}
.foot-col li{list-style:none;font-size:24px;height:70px;display:flex;align-items:flex-start;gap:18px;white-space:nowrap}
.tri{width:0;height:0;border-top:11px solid transparent;border-bottom:11px solid transparent;border-left:16px solid var(--white);margin-top:3px}
.dot{width:38px;height:38px;border-radius:50%;background:var(--white);margin-top:-6px}
.dot.blue{background:var(--blue-deep)}.dot.sky{background:var(--blue)}.dot.red{background:var(--red)}.dot.grey{background:#d8d8d8}
.copyright{left:0;top:4024px;width:1200px;text-align:center;color:var(--white);font-size:20px;font-weight:600}
.copyright b{color:var(--blue)}
</style>
</head>
<body>
<div class="canvas">

<svg width="0" height="0" style="position:absolute">
  <defs>
    <symbol id="car" viewBox="0 0 120 80"><path d="M18 48 L30 26 Q33 20 40 20 H80 Q87 20 90 26 L102 48 Q110 50 110 58 V66 H10 V58 Q10 50 18 48Z" fill="currentColor"/><path d="M34 46 L42 28 H78 L86 46Z" fill="#fff"/><circle cx="32" cy="68" r="9" fill="currentColor"/><circle cx="88" cy="68" r="9" fill="currentColor"/></symbol>
    <symbol id="boat" viewBox="0 0 120 80"><path d="M10 52 H110 L96 72 H24Z" fill="currentColor"/><rect x="34" y="30" width="52" height="18" fill="currentColor"/><rect x="44" y="14" width="32" height="14" fill="currentColor"/><rect x="40" y="35" width="8" height="8" fill="#fff"/><rect x="56" y="35" width="8" height="8" fill="#fff"/><rect x="72" y="35" width="8" height="8" fill="#fff"/></symbol>
    <symbol id="plane" viewBox="0 0 160 80"><path d="M10 42 Q10 34 30 34 H140 Q154 38 154 42 Q154 46 140 50 H30 Q10 50 10 42Z" fill="currentColor"/><path d="M66 36 L96 8 H106 L92 36Z M66 48 L96 76 H106 L92 48Z M128 36 L140 20 H148 L142 36Z" fill="currentColor"/></symbol>
    <symbol id="truck" viewBox="0 0 120 80"><rect x="24" y="8" width="72" height="58" rx="6" fill="currentColor"/><rect x="34" y="18" width="52" height="20" fill="#fff"/><rect x="30" y="46" width="14" height="6" fill="#fff"/><rect x="76" y="46" width="14" height="6" fill="#fff"/><rect x="30" y="66" width="14" height="10" fill="currentColor"/><rect x="76" y="66" width="14" height="10" fill="currentColor"/></symbol>
    <symbol id="sparkle" viewBox="0 0 20 20"><path d="M10 0 L12 8 L20 10 L12 12 L10 20 L8 12 L0 10 L8 8Z" fill="currentColor"/></symbol>
    <symbol id="wash" viewBox="0 0 150 140"><rect x="2" y="10" width="12" height="130" fill="currentColor"/><rect x="136" y="10" width="12" height="130" fill="currentColor"/><rect x="2" y="4" width="146" height="10" fill="currentColor"/><path d="M40 24 q4 8 0 10 q-4-2 0-10Z M75 24 q4 8 0 10 q-4-2 0-10Z M110 24 q4 8 0 10 q-4-2 0-10Z" fill="currentColor"/><g fill="currentColor"><rect x="18" y="36" width="8" height="4"/><rect x="18" y="56" width="8" height="4"/><rect x="18" y="76" width="8" height="4"/><rect x="18" y="96" width="8" height="4"/><rect x="18" y="116" width="8" height="4"/><rect x="124" y="36" width="8" height="4"/><rect x="124" y="56" width="8" height="4"/><rect x="124" y="76" width="8" height="4"/><rect x="124" y="96" width="8" height="4"/><rect x="124" y="116" width="8" height="4"/></g></symbol>
  </defs>
</svg>

<!-- header -->
<header class="site-header abs">
  <svg class="header-band abs" width="1200" height="142" viewBox="0 0 1200 142" aria-hidden="true">
    <polygon points="400,0 1200,0 1200,86 320,86" fill="var(--blue-deep)"/>
    <polygon points="470,86 1200,86 1200,142 400,142" fill="var(--navy)"/>
  </svg>
  <div class="brand abs"><span class="brand-dot"></span><span class="brand-name">Steady Harbor Detailing</span></div>
  <div class="header-phone abs">
    <svg width="36" height="36" viewBox="0 0 24 24"><path fill="#fff" d="M6.6 10.8a15.1 15.1 0 006.6 6.6l2.2-2.2c.3-.3.7-.4 1-.2 1.1.4 2.3.6 3.6.6.6 0 1 .4 1 1V20c0 .6-.4 1-1 1A17 17 0 013 4c0-.6.4-1 1-1h3.5c.6 0 1 .4 1 1 0 1.3.2 2.5.6 3.6.1.3 0 .7-.2 1z"/></svg>
    772-555-0148
  </div>
  <div class="social-top abs"><span></span><span></span><span></span><span></span></div>
  <nav class="main-nav abs">
    <a href="#">HOME</a><a href="#" class="active">ABOUT US</a><a href="#">SERVICES ˅</a><a href="#">CONTACT</a>
  </nav>
</header>

<!-- about -->
<div class="about-bg photo-dark abs" role="img" aria-label="Dark photo of a detailer polishing a vehicle in a garage"></div>
<h1 class="about-title abs">ABOUT US</h1>
<div class="story-tag abs"><i></i>OUR STORY<i></i></div>
<div class="about-copy abs">
  <p>Lorem ipsum dolor sit amet, consectetuer adipiscing elit, sed diam nonummy nibh euismod tincidunt ut laoreet dolore magna aliquam erat volutpat. Ut wisi enim ad minim veniam, quis nostrud exerci tation ullamcorper suscipit lobortis nisl ut aliquip ex ea commodo consequat. Duis autem vel eum iriure dolor in hendrerit in vulputate velit esse molestie consequat, vel illum dolore eu feugiat nulla facilisis at vero eros et accumsan et iusto odio dignissim qui blandit praesent luptatum zzril delenit augue duis dolore te.</p>
  <p>Lorem ipsum dolor sit amet, consectetuer adipiscing elit, sed diam nonummy nibh euismod tincidunt ut laoreet dolore magna aliquam erat volutpat. Ut wisi enim ad minim veniam, quis nostrud exerci tation ullamcorper suscipit lobortis nisl ut aliquip ex ea.</p>
  <p>Lorem ipsum dolor sit amet, consectetuer adipiscing elit, sed diam nonummy nibh euismod tincidunt ut laoreet dolore magna aliquam erat volutpat. Ut wisi enim ad minim veniam, quis nostrud exerci tation ullamcorper suscipit lobortis nisl ut aliquip ex ea commodo consequat. Duis autem vel eum iriure dolor in hendrerit in vulputate velit esse molestie consequat, vel illum dolore eu feugiat nulla facilisis at vero eros et accumsan et iusto odio dignissim qui blandit praesent luptatum zzril delenit augue duis dolore te.</p>
  <p>Lorem ipsum dolor sit amet, consectetuer adipiscing elit, sed diam nonummy nibh euismod tincidunt ut laoreet dolore magna aliquam erat volutpat. Ut wisi enim ad minim veniam, quis nostrud exerci tation ullamcorper suscipit lobortis nisl ut aliquip ex ea.</p>
  <p>Lorem ipsum dolor sit amet, consectetuer adipiscing elit, sed diam nonummy nibh euismod tincidunt ut laoreet dolore magna aliquam erat volutpat. Ut wisi enim ad minim veniam, quis nostrud exerci tation ullamcorper suscipit lobortis nisl ut aliquip ex ea commodo consequat. Duis autem vel eum iriure dolor in hendrerit in vulputate velit esse molestie consequat, vel illum dolore eu feugiat nulla facilisis at vero eros et accumsan et iusto odio dignissim qui blandit praesent luptatum zzril delenit augue duis dolore te.</p>
  <p>Lorem ipsum dolor sit amet, consectetuer adipiscing elit, sed diam nonummy nibh euismod tincidunt ut laoreet dolore magna aliquam erat volutpat. Ut wisi enim ad minim veniam, quis nostrud exerci tation ullamcorper suscipit lobortis nisl ut aliquip ex ea.</p>
</div>

<h2 class="mech-title abs">OUR MECHANICS</h2>
<div class="mech-card abs" style="left:44px"><div class="mech-photo" role="img" aria-label="Portrait photo of a team member in blue overalls"></div><div class="mech-name">Sample Name</div><div class="mech-role">Team Role Goes Here</div></div>
<div class="mech-card abs" style="left:328px"><div class="mech-photo" role="img" aria-label="Portrait photo of a team member in blue overalls"></div><div class="mech-name">Sample Name</div><div class="mech-role">Team Role Goes Here</div></div>
<div class="mech-card abs" style="left:615px"><div class="mech-photo" role="img" aria-label="Portrait photo of a team member in blue overalls"></div><div class="mech-name">Sample Name</div><div class="mech-role">Team Role Goes Here</div></div>
<div class="mech-card abs" style="left:896px"><div class="mech-photo" role="img" aria-label="Portrait photo of a team member in blue overalls"></div><div class="mech-name">Sample Name</div><div class="mech-role">Team Role Goes Here</div></div>

<!-- what we do background -->
<div class="work-bg photo-dark abs" role="img" aria-label="Dark photo of a car being washed with a pressure hose"></div>

<!-- booking -->
<div class="booking abs">
  <div class="select abs" style="left:22px">Select Vehicle<span class="caret">˅</span></div>
  <div class="select abs" style="left:399px">
    <svg width="20" height="26" viewBox="0 0 20 26"><path d="M10 0a10 10 0 00-10 10c0 7 10 16 10 16s10-9 10-16A10 10 0 0010 0zm0 14a4 4 0 110-8 4 4 0 010 8z" fill="var(--navy)"/></svg>
    Select Location<span class="caret">˅</span></div>
  <div class="btn btn-blue abs">GET AN APPOINTMENT</div>
  <div class="btn btn-red abs">CONTACT US</div>
  <div class="call-label abs">OR CALL US NOW!</div>
  <div class="call-number abs">772-555-0148</div>
</div>

<h2 class="work-title abs">WHAT WE DO?</h2>
<p class="work-copy abs">Lorem ipsum dolor sit amet, consectetur adipisicing elit, sed do eiusmod tempor incididunt ut labore et dolore magna aliqua. Ut enim ad minim veniam, quis nostrud exercitation ullamco laboris nisi ut aliquip ex ea commodo consequat. Duis aute irure dolor in reprehenderit in velit esse cillum dolore eu fugiat nulla pariatur. Excepteur sint occaecat cupidatat non proident.</p>

<div class="service abs" style="left:48px;top:2337px"><svg width="140" height="136" viewBox="0 0 140 136" style="color:var(--blue)"><use href="#sparkle" x="30" y="4" width="20" height="20"/><use href="#sparkle" x="90" y="0" width="14" height="14"/><use href="#car" x="10" y="40" width="120" height="90"/></svg>CAR WAX</div>
<div class="service abs" style="left:329px;top:2337px"><svg width="140" height="136" viewBox="0 0 140 136" style="color:var(--blue)"><use href="#sparkle" x="30" y="4" width="20" height="20"/><use href="#sparkle" x="92" y="0" width="14" height="14"/><use href="#boat" x="10" y="40" width="120" height="90"/></svg>BOAT WAX</div>
<div class="service abs" style="left:608px;top:2337px"><svg width="200" height="136" viewBox="0 0 200 136" style="color:var(--blue)"><use href="#sparkle" x="40" y="4" width="20" height="20"/><use href="#sparkle" x="140" y="0" width="14" height="14"/><use href="#plane" x="10" y="40" width="180" height="90"/></svg>AIRPLANE WAX</div>
<div class="service abs" style="left:889px;top:2337px"><svg width="140" height="136" viewBox="0 0 140 136" style="color:var(--blue)"><use href="#sparkle" x="30" y="4" width="20" height="20"/><use href="#sparkle" x="92" y="0" width="14" height="14"/><use href="#truck" x="10" y="40" width="120" height="90"/></svg>TRUCK WAX</div>

<div class="service abs" style="left:48px;top:2605px"><svg width="150" height="140" viewBox="0 0 150 140" style="color:var(--blue)"><use href="#wash" x="0" y="0" width="150" height="140"/><use href="#car" x="27" y="48" width="96" height="80"/></svg>CAR WASH</div>
<div class="service abs" style="left:329px;top:2605px"><svg width="150" height="140" viewBox="0 0 150 140" style="color:var(--blue)"><use href="#sparkle" x="40" y="4" width="14" height="14"/><use href="#sparkle" x="96" y="4" width="14" height="14"/><use href="#boat" x="15" y="40" width="120" height="96"/></svg>BOAT WASH</div>
<div class="service abs" style="left:608px;top:2605px"><svg width="200" height="140" viewBox="0 0 200 140" style="color:var(--blue)"><use href="#sparkle" x="70" y="4" width="14" height="14"/><use href="#sparkle" x="116" y="4" width="14" height="14"/><use href="#plane" x="10" y="40" width="180" height="96"/></svg>AIRPLANE WASH</div>
<div class="service abs" style="left:889px;top:2605px"><svg width="150" height="140" viewBox="0 0 150 140" style="color:var(--blue)"><use href="#wash" x="0" y="0" width="150" height="140"/><use href="#truck" x="27" y="44" width="96" height="86"/></svg>TRUCK WASH</div>

<!-- who we are -->
<h2 class="who-title abs">WHO WE ARE?</h2>
<p class="who-copy abs">Spare tip hamburger cow ribs ham jowl chicken andouille ham flank pig pig belly brisket cow loin ham tenderloin. Leberkas steak ball brisket strip.</p>

<div class="care abs" style="left:40px">
  <svg width="200" height="226" viewBox="0 0 200 226"><polygon points="100,6 194,58 194,168 100,220 6,168 6,58" fill="var(--white)" stroke="var(--navy)" stroke-width="12"/><g style="color:var(--red)"><use href="#plane" x="30" y="70" width="140" height="80"/></g></svg>
  <h3>We Care For You</h3><p>lorem ipsum door akis<br>amet, lorem dolor dolor</p>
</div>
<div class="care abs" style="left:324px">
  <svg width="200" height="226" viewBox="0 0 200 226"><polygon points="100,6 194,58 194,168 100,220 6,168 6,58" fill="var(--white)" stroke="var(--navy)" stroke-width="12"/><g fill="var(--red)"><rect x="44" y="76" width="78" height="52"/><path d="M124 90 H146 L160 108 V128 H124Z"/><circle cx="64" cy="134" r="10"/><circle cx="140" cy="134" r="10"/></g></svg>
  <h3>We Care For You</h3><p>lorem ipsum door akis<br>amet, lorem dolor dolor</p>
</div>
<div class="care abs" style="left:608px">
  <svg width="200" height="226" viewBox="0 0 200 226"><polygon points="100,6 194,58 194,168 100,220 6,168 6,58" fill="var(--white)" stroke="var(--navy)" stroke-width="12"/><g style="color:var(--red)"><use href="#boat" x="36" y="66" width="128" height="86"/></g></svg>
  <h3>We Care For You</h3><p>lorem ipsum door akis<br>amet, lorem dolor dolor</p>
</div>
<div class="care abs" style="left:889px">
  <svg width="200" height="226" viewBox="0 0 200 226"><polygon points="100,6 194,58 194,168 100,220 6,168 6,58" fill="var(--white)" stroke="var(--navy)" stroke-width="12"/><g style="color:var(--red)"><use href="#car" x="40" y="68" width="120" height="80"/></g></svg>
  <h3>We Care For You</h3><p>lorem ipsum door akis<br>amet, lorem dolor dolor</p>
</div>

<!-- footer -->
<div class="footer-bg abs" role="img" aria-label="Dark photo of a freshly washed vehicle"></div>
<div class="foot-col abs" style="left:118px">
  <h4>OUR SERVICES</h4>
  <ul><li><span class="tri"></span>Car Detailing</li><li><span class="tri"></span>Truck Detailing</li><li><span class="tri"></span>Boat Detailing</li><li><span class="tri"></span>Airplane Detailing</li></ul>
</div>
<div class="foot-col abs" style="left:459px">
  <h4>CONTACT US</h4>
  <ul><li>772-555-0148</li><li>hello@steadyharbor.example</li><li>1234 Sample Address, Here</li></ul>
</div>
<div class="foot-col abs" style="left:839px">
  <h4>LIKE US ON</h4>
  <ul><li><span class="dot blue"></span>friendsnook.com</li><li><span class="dot sky"></span>chirpline.com</li><li><span class="dot red"></span>pinboardly.com</li><li><span class="dot grey"></span>snapframe.com</li></ul>
</div>
<div class="copyright abs">© Copyrights 2018 <b>Steady Harbor Detailing</b> | All Rights Reserved.</div>

</div>
</body>
</html>
```